Business Card Design & Gift cards, Gift Cert, Donation Card

Retail Gift Store-in addition to Business Cards we'd like sequenced 2 sided Gift cards, Gift Certificate Cards, and Donation Cards.please see examples and email for clarificationlogos attached with examples-
Gift Card, Gift Certificate and Donation Card will all be same style just differant upper right title, with back side info as example.
business card, as example is single sided.
looking for additional ideas for layout

Industry/Entity Type

Business

Contact Information for Business Card

211 Newman St.East Tawas, MI 48730989.362.8730Office@BrewKrew.com

Requirements
Must have
• Blue as per example
• Logos provided
• like gradiant background

```html
<!DOCTYPE html>
<html lang="en">
<head>
<meta charset="utf-8">
<title>Tillow Marsh – Business Card &amp; Gift Card</title>
<link rel="stylesheet" href="https://fonts.googleapis.com/css2?family=Comic+Neue:wght@400;700&display=swap">
<style>
  :root {
    --backdrop: #3a3a3a;
    --card: #ffffff;
    --ink: #111111;
    --ink-soft: #555555;
    --rule: #333333;
    --brand-blue: #1a2fc8;
    --brand-sun: #f4e21a;
    --faint-blue: #e8ecfb;
    --faint-sun: #fbf6d6;
  }
  html, body {
    margin: 0;
    padding: 0;
    width: 1105px;
    height: 1200px;
    overflow: hidden;
    background: var(--backdrop);
  }
  body { position: relative; font-family: "Comic Neue", "Comic Sans MS", cursive; }
  .card {
    position: absolute;
    left: 196px;
    width: 720px;
    height: 412px;
    background: var(--card);
    border-radius: 25px;
    box-shadow: 0 8px 14px rgba(0,0,0,0.55);
    overflow: hidden;
  }
  .card--front { top: 146px; }
  .card--back { top: 602px; }
  .card * { position: absolute; margin: 0; white-space: nowrap; }

  .brand-mark-area {
    left: 345px; top: 0;
    width: 375px; height: 412px;
    background: linear-gradient(160deg, var(--brand-blue) 0%, #3a52d6 55%, var(--brand-sun) 100%);
  }
  .brand-mark-faint {
    left: 232px; top: 33px;
    width: 324px; height: 352px;
    background: linear-gradient(160deg, var(--faint-blue) 0%, var(--faint-blue) 55%, var(--faint-sun) 100%);
  }

  .brand-name {
    left: 36px; top: 38px;
    font-size: 40px; font-weight: 400;
    color: var(--ink); letter-spacing: 0.5px;
  }
  .contact { left: 36px; top: 120px; font-size: 21px; line-height: 27.5px; color: var(--ink-soft); }
  .contact ul { position: static; padding: 0; }
  .contact li { position: static; list-style: none; display: flex; align-items: center; gap: 8px; }
  .contact svg { position: static; width: 16px; height: 16px; fill: var(--ink-soft); }
  .offerings { left: 36px; top: 276px; font-size: 21px; line-height: 26px; color: var(--ink-soft); }
  .offerings span { position: static; display: block; }

  .card-number { right: 34px; top: 36px; font-size: 18px; color: var(--ink); }
  .field { left: 0; width: 100%; height: 40px; }
  .field-label { top: 0; font-size: 24px; color: var(--ink); }
  .field-label.small { font-size: 22px; }
  .field-line { height: 0; border-top: 1.5px solid var(--rule); }
</style>
</head>
<body>

<section class="card card--front" aria-label="Business card front">
  <div class="brand-mark-area" role="img" aria-label="Brand mark: blue figure stepping over a yellow rising sun"></div>
  <h1 class="brand-name">TILLOW MARSH</h1>
  <div class="contact">
    <ul>
      <li>482 Larkfield Ave.</li>
      <li>Pine Hollow, MI 48731</li>
      <li><svg viewBox="0 0 16 16" aria-hidden="true"><path d="M3.5 1.5l2.5 0 1.2 3.3-1.7 1.3a8 8 0 0 0 4.4 4.4l1.3-1.7 3.3 1.2v2.5c0 .8-.7 1.5-1.5 1.5A12.5 12.5 0 0 1 2 3c0-.8.7-1.5 1.5-1.5z"/></svg>989.517.4296</li>
      <li><svg viewBox="0 0 16 16" aria-hidden="true"><path d="M1 3.5h14v9H1z M1.5 4l6.5 5 6.5-5" fill="var(--ink-soft)" stroke="#fff" stroke-width="1"/></svg>Office@TillowMarsh.com</li>
      <li><svg viewBox="0 0 16 16" aria-hidden="true"><circle cx="8" cy="8" r="7"/><path d="M1 8h14M8 1c-3 3.5-3 10.5 0 14M8 1c3 3.5 3 10.5 0 14" stroke="#fff" stroke-width="1" fill="none"/></svg>www.TillowMarsh.com</li>
    </ul>
  </div>
  <p class="offerings">
    <span>Gourmet Food</span>
    <span>Fine Wines | Gift Baskets</span>
    <span>Kitchen &amp; Bath Accessories</span>
    <span>Candles | Cards | Soaps</span>
  </p>
</section>

<section class="card card--back" aria-label="Gift card back">
  <div class="brand-mark-faint" role="img" aria-label="Faint brand mark: figure over rising sun"></div>
  <p class="card-number">Card Number : 58724</p>

  <div class="field" style="top:88px">
    <span class="field-label" style="left:58px">To :</span>
    <span class="field-line" style="left:126px;width:541px;top:17px"></span>
  </div>
  <div class="field" style="top:142px">
    <span class="field-label" style="left:58px">Form :</span>
    <span class="field-line" style="left:153px;width:514px;top:20px"></span>
  </div>
  <div class="field" style="top:225px">
    <span class="field-label small" style="left:56px">Date&nbsp; Issued :</span>
    <span class="field-line" style="left:206px;width:471px;top:20px"></span>
  </div>
  <div class="field" style="top:273px">
    <span class="field-label small" style="left:56px">Expiration Date :</span>
    <span class="field-line" style="left:236px;width:441px;top:20px"></span>
  </div>
  <div class="field" style="top:321px">
    <span class="field-label small" style="left:56px">Employee :</span>
    <span class="field-line" style="left:187px;width:490px;top:20px"></span>
  </div>
</section>

</body>
</html>
```